Need business card with a logo for a hearing aid sales and audiology business. We have two Hearing Instrument Specialists and one Audiologist on staff. Over 25 years in business. Locally owned and operated. Financing available. Most insurances accepted.

Summit Audio Wellness LLC
48730 W Larchmont, Suite 7
Spokane, WA 99281
509-617-2084
www.summitaudiowell.example

Manager
Tobias Kerrell HIS COHC
License #71829046

Target Market(s)

50yr old + people with a hearing loss.

Industry/Entity Type

Business

Contact Information for Business Card

48730 W Larchmont, Suite 7
Spokane, WA 99281
509-617-2084
www.summitaudiowell.example

Manager
Tobias Kerrell HIS COHC
NLVE #71829046

Font styles to use
Serif
Sans Serif

Requirements
Must have
• Business name, Tobias's name and title(s) and contact information, License #, web address

```html
<!DOCTYPE html>
<html lang="en">
<head>
<meta charset="utf-8">
<title>Summit Audio Wellness LLC – Business Card</title>
<link rel="stylesheet" href="https://fonts.googleapis.com/css2?family=Alegreya+Sans:wght@500&family=Alegreya+Sans+SC:wght@400;500&family=Fira+Sans+Extra+Condensed:wght@700&family=Source+Sans+3:wght@400&display=swap">
<style>
  :root {
    --brand-navy: #2c4a9b;
    --brand-sky: #1ba4e6;
    --brand-green: #2a9a3c;
    --text-grey: #5f6062;
    --text-dark: #1e1e1e;
    --card-white: #ffffff;
    --band-top: #12a3e4;
    --band-light: #c4e8fb;
    --band-bottom: #8dd2f4;
  }
  * { box-sizing: border-box; margin: 0; padding: 0; }
  html, body {
    width: 1200px;
    height: 758px;
    overflow: hidden;
    background: var(--card-white);
  }
  .business-card {
    position: relative;
    width: 1200px;
    height: 758px;
    background: var(--card-white);
  }
  .brand-mark {
    position: absolute;
    left: 150px;
    top: 112px;
    display: flex;
    align-items: center;
    gap: 22px;
  }
  .brand-mark__dot {
    width: 64px;
    height: 64px;
    border-radius: 50%;
    background: var(--brand-green);
  }
  .brand-mark__name {
    font-family: "Fira Sans Extra Condensed", sans-serif;
    font-weight: 700;
    font-size: 50px;
    letter-spacing: 3px;
    color: var(--brand-navy);
  }
  .manager {
    position: absolute;
    right: 95px;
    top: 58px;
    text-align: right;
  }
  .manager__name {
    font-family: "Alegreya Sans", sans-serif;
    font-weight: 500;
    font-size: 50px;
    line-height: 1;
    color: var(--brand-sky);
    letter-spacing: -0.5px;
  }
  .manager__role {
    margin-top: 2px;
    margin-right: 22px;
    font-family: "Alegreya Sans SC", sans-serif;
    font-weight: 400;
    font-size: 44px;
    line-height: 1;
    color: var(--text-grey);
    letter-spacing: 1px;
  }
  .manager__license {
    font-family: "Alegreya Sans", sans-serif;
    font-style: italic;
    font-size: 22px;
    letter-spacing: 0;
  }
  .company-name {
    position: absolute;
    left: 0;
    right: 0;
    top: 280px;
    text-align: center;
    font-family: "Fira Sans Extra Condensed", sans-serif;
    font-weight: 700;
    font-size: 50px;
    letter-spacing: -0.5px;
    color: var(--brand-navy);
  }
  .contact {
    position: absolute;
    display: flex;
    align-items: center;
    gap: 16px;
    font-family: "Alegreya Sans SC", sans-serif;
    font-weight: 500;
    font-size: 33px;
    line-height: 1.25;
    color: var(--brand-navy);
  }
  .contact__icon { width: 50px; height: 44px; flex: none; fill: var(--brand-navy); }
  .contact--address { left: 138px; top: 443px; }
  .contact--phone { left: 742px; top: 466px; }
  .web-band {
    position: absolute;
    left: 0;
    right: 0;
    bottom: 0;
    height: 110px;
    background: linear-gradient(to bottom, var(--band-top) 0%, var(--band-top) 12%, var(--band-light) 42%, var(--band-light) 60%, var(--band-bottom) 100%);
    display: flex;
    align-items: center;
    justify-content: center;
    padding-top: 8px;
  }
  .web-band__url {
    font-family: "Source Sans 3", sans-serif;
    font-size: 35px;
    color: var(--text-dark);
  }
</style>
</head>
<body>
  <main class="business-card">
    <div class="brand-mark">
      <span class="brand-mark__dot"></span>
      <span class="brand-mark__name">SAW</span>
    </div>

    <div class="manager">
      <p class="manager__name">Tobias Kerrell HIS COHC</p>
      <p class="manager__role">Manager <span class="manager__license">(NLVE #71829046)</span></p>
    </div>

    <h1 class="company-name">Summit Audio Wellness LLC</h1>

    <address class="contact contact--address" style="font-style:normal">
      <svg class="contact__icon" viewBox="0 0 50 44" aria-hidden="true">
        <path d="M25 2 L2 22 L7 26 L25 10 L43 26 L48 22 Z"/>
        <path d="M10 26 L25 13 L40 26 L40 42 L30 42 L30 31 L20 31 L20 42 L10 42 Z"/>
      </svg>
      <span>48730 W Larchmont, Suite 7<br>Spokane, WA 99281</span>
    </address>

    <div class="contact contact--phone">
      <svg class="contact__icon" viewBox="0 0 50 44" aria-hidden="true">
        <path d="M2 12 C2 4 48 4 48 12 L48 17 L37 17 L37 12 C30 10 20 10 13 12 L13 17 L2 17 Z"/>
        <path d="M16 14 L34 14 L44 38 C44 41 42 42 40 42 L10 42 C8 42 6 41 6 38 Z"/>
        <g fill="#ffffff">
          <rect x="18" y="22" width="3" height="3"/><rect x="23.5" y="22" width="3" height="3"/><rect x="29" y="22" width="3" height="3"/>
          <rect x="18" y="27" width="3" height="3"/><rect x="23.5" y="27" width="3" height="3"/><rect x="29" y="27" width="3" height="3"/>
          <rect x="18" y="32" width="3" height="3"/><rect x="23.5" y="32" width="3" height="3"/><rect x="29" y="32" width="3" height="3"/>
        </g>
      </svg>
      <span>Tel: 509-617-2084</span>
    </div>

    <footer class="web-band">
      <span class="web-band__url">www.summitaudiowell.example</span>
    </footer>
  </main>
</body>
</html>
```